Penfield Draft Works (PDWorks.net)

We need a Wordpress-based site designed for a client who provides writing and editing services for the IT industry. We have a wireframe complete for the homepage, but need all internal pages designed (based on homepage wireframe) and the entire site coded for WP.

Internal pages include: "Our Work" (with samples & testimonials); "Capabilities" (with sections to address "strategy", "coaching", "writing" and "editing"); "About Us"; and a Contact page.

Will provide all copywriting, writing samples, testimonials, and client logos.

We completely realize/acknowledge the subject matter is visually BORING! Anything at all that can be done to make it look visually appealing would be *great*! Stock photography is fine.

Please feel free to ask any questions whatsoever. Thanks for your time!

```html
<!DOCTYPE html>
<html lang="en">
<head>
<meta charset="utf-8">
<title>Penfield Draft Works</title>
<link href="https://fonts.googleapis.com/css2?family=Roboto:wght@400;500;700&display=swap" rel="stylesheet">
<style>
:root{
  --blue:#1f5ba8;
  --blue-deep:#1a4f9c;
  --orange:#f47b20;
  --ink:#1d1d1d;
  --text:#444;
  --white:#fff;
  --grey:#eeeeee;
}
*{box-sizing:border-box;margin:0;padding:0}
html,body{width:1200px;height:3126px;overflow:hidden}
body{font-family:'Roboto',sans-serif;color:var(--text);background:var(--white);position:relative}
.btn{display:inline-flex;align-items:center;justify-content:center;background:var(--orange);color:var(--white);font-weight:500;font-size:16px;border-radius:26px;text-transform:uppercase}
.heading{font-weight:700;color:var(--ink);text-transform:uppercase;text-align:center;font-size:32px;line-height:41px}
.rule{width:64px;height:3px;background:var(--orange);margin:12px auto 0}
.photo{display:block}

/* header */
.site-header{position:absolute;top:0;left:0;width:1200px;height:80px;display:flex;align-items:center}
.brand{position:absolute;left:128px;top:12px;width:226px;text-align:center;color:var(--blue);font-weight:700;font-size:24px;line-height:28px;text-transform:uppercase}
.nav{position:absolute;left:410px;top:30px;display:flex;gap:42px;font-size:14px;font-weight:500;color:var(--ink)}
.nav-cta{position:absolute;left:908px;top:13px;width:161px;height:51px}

/* hero */
.hero{position:absolute;top:80px;left:0;width:1200px;height:600px;background:linear-gradient(115deg,#2b2e33 0%,#5a4a3c 45%,#7b5536 70%,#3a2a20 100%)}
.hero-box{position:absolute;left:193px;top:158px;width:780px;height:276px;background:rgba(40,40,40,.55);text-align:center;color:var(--white)}
.hero-box h1{font-size:40px;line-height:56px;font-weight:700;text-transform:uppercase;margin-top:24px}
.hero-box p{font-size:14px;line-height:28px;margin:10px 60px 0}
.hero-box .btn{width:160px;height:50px;margin-top:14px}
.dots{position:absolute;top:543px;left:564px;display:flex;gap:6px}
.dots span{width:14px;height:14px;border-radius:50%;border:2px solid var(--orange)}
.dots span.on{background:var(--orange)}

/* services */
.value{position:absolute;top:755px;left:0;width:1200px}
.cards{position:absolute;top:131px;left:116px;display:flex;gap:20px}
.card{width:227px;height:331px;background:var(--white);border-radius:6px;box-shadow:0 2px 10px rgba(0,0,0,.1);text-align:center;overflow:hidden}
.card h3{height:41px;line-height:46px;font-size:20px;font-weight:500;color:var(--blue);text-transform:uppercase}
.card .photo{height:160px;background:linear-gradient(135deg,#c9ccd0,#8a8f96)}
.card p{font-size:13px;line-height:25px;padding:14px 8px 0}
.card.active{background:var(--orange);color:var(--white)}
.card.active h3{color:var(--white)}

/* clients */
.clients{position:absolute;top:1308px;left:0;width:1200px;height:320px;background:linear-gradient(120deg,#2a66b8,#1d5aac)}
.clients .heading{color:var(--white);margin-top:67px}
.logos{position:absolute;top:158px;left:132px;display:flex;gap:8px}
.logo{width:149px;height:69px;background:var(--white);display:flex;align-items:center;justify-content:center;gap:6px;font-size:14px;font-weight:500;color:var(--ink)}
.logo i{width:12px;height:12px;background:var(--blue);border-radius:50%}

/* work */
.work{position:absolute;top:1703px;left:0;width:1200px}
.work-cards{position:absolute;top:79px;left:131px;display:flex;gap:15px}
.work-card{width:303px;height:411px;text-align:center}
.work-card.lift{box-shadow:0 3px 14px rgba(0,0,0,.15)}
.work-card .photo{height:193px;background:linear-gradient(135deg,#3d5870,#b9b3a6)}
.work-card h4{font-size:15px;line-height:28px;font-weight:700;color:#333;text-transform:uppercase;margin-top:12px;padding:0 8px}
.work-card p{font-size:13.5px;line-height:28px;padding:4px 10px 0}
.mark{display:flex;align-items:center;justify-content:center;gap:6px;margin-top:10px;font-size:13px;font-weight:700;color:#333}
.mark i{width:10px;height:10px;background:#c62828}
.work-btn{position:absolute;top:550px;left:507px;width:186px;height:50px}

/* contact */
.cta{position:absolute;top:2380px;left:0;width:1200px;height:430px;display:flex}
.cta-col{width:600px;height:430px;text-align:center;color:var(--white);padding-top:42px}
.cta-left{background:linear-gradient(135deg,#2d72c8,#1a56a6)}
.cta-right{background:linear-gradient(135deg,#1b4f98,#164488)}
.cta-col h2{font-size:32px;line-height:50px;font-weight:700;text-transform:uppercase}
.cta-col p{font-size:14px;line-height:28px;margin:6px 70px 0}
.cta-left .btn{width:186px;height:50px;margin-top:22px}
.email{width:450px;height:48px;margin:20px auto 0;background:var(--white);border-radius:24px;color:#888;font-style:italic;font-size:14px;line-height:48px}
.cta-right .btn{width:186px;height:50px;margin-top:10px}

/* footer */
.site-footer{position:absolute;top:2810px;left:0;width:1200px;height:250px}
.foot-brand{position:absolute;left:106px;top:92px;width:244px;text-align:center;font-size:24px;line-height:28px;font-weight:700;color:var(--blue);text-transform:uppercase}
.social{position:absolute;left:127px;top:165px;display:flex;gap:17px}
.social span{width:38px;height:38px;border-radius:50%;background:var(--orange)}
.foot-col{position:absolute;top:70px;font-size:13.5px;color:#333}
.foot-col h5{font-size:15px;font-weight:500;color:var(--blue);text-transform:uppercase;margin-bottom:8px}
.foot-col li{list-style:none;line-height:28px;display:flex;align-items:center;gap:8px}
.chev{color:var(--orange);font-size:12px}
.contact li{align-items:flex-start;margin-bottom:10px}
.copyright{position:absolute;top:3060px;left:0;width:1200px;height:66px;background:var(--grey);text-align:center;line-height:66px;font-size:13.5px;color:#333}
.copyright b{color:var(--blue);font-weight:500}
</style>
</head>
<body>

<header class="site-header">
  <div class="brand">Penfield Draft<br>Works</div>
  <nav class="nav"><span>HOME</span><span>OUR WORK</span><span>CAPABILITIES</span><span>ABOUT US</span><span>BLOG</span></nav>
  <span class="btn nav-cta">Get in touch</span>
</header>

<section class="hero" role="img" aria-label="Photo of a hand writing with a pen on paper beside a laptop">
  <div class="hero-box">
    <h1>Communicate your expertise and<br>your customer successes</h1>
    <p>Lorem ipsum dolor sit amet, consectetur adipiscing elit, sed do eiusmod tempor incididunt ut labore et dolore magna aliqua. Quis ipsum suspendisse ultrices gravida.</p>
    <span class="btn">Get in touch</span>
  </div>
  <div class="dots"><span class="on"></span><span></span><span></span><span></span></div>
</section>

<section class="value">
  <h2 class="heading">Text copy that explains in concise, snappy terms<br>the value you provide to customers.</h2>
  <div class="rule"></div>
  <div class="cards">
    <article class="card"><h3>Strategy</h3><div class="photo" role="img" aria-label="Photo of a team planning around a table"></div><p>Lorem ipsum dolor sit amet, consec-tetur adipiscing elit, sed do eiusmod tempor incididunt ut labore et dolore magna.</p></article>
    <article class="card active"><h3>Coaching</h3><div class="photo" role="img" aria-label="Photo of two colleagues in a coaching session"></div><p>Lorem ipsum dolor sit amet, consec-tetur adipiscing elit, sed do eiusmod tempor incididunt ut labore et dolore magna.</p></article>
    <article class="card"><h3>Writing</h3><div class="photo" role="img" aria-label="Photo of a hand writing on a page"></div><p>Lorem ipsum dolor sit amet, consec-tetur adipiscing elit, sed do eiusmod tempor incididunt ut labore et dolore magna.</p></article>
    <article class="card"><h3>Editing</h3><div class="photo" role="img" aria-label="Photo of a document being marked up with a red pen"></div><p>Lorem ipsum dolor sit amet, consec-tetur adipiscing elit, sed do eiusmod tempor incididunt ut labore et dolore magna.</p></article>
  </div>
</section>

<section class="clients">
  <h2 class="heading">A selection of past and current clients</h2>
  <div class="rule"></div>
  <div class="logos">
    <div class="logo"><i></i>Northgate</div>
    <div class="logo"><i></i>Larkline</div>
    <div class="logo"><i></i>Quillmetric</div>
    <div class="logo"><i></i>Hexform</div>
    <div class="logo"><i></i>Brightvane</div>
    <div class="logo"><i></i>Corvane</div>
  </div>
</section>

<section class="work">
  <h2 class="heading">Text highlighting the type of work you do</h2>
  <div class="rule"></div>
  <div class="work-cards">
    <article class="work-card"><div class="photo" role="img" aria-label="Photo of a hand signing a document"></div><h4>Lorem ipsum dolor sit amet con sectetur adipiscing elit.</h4><p>Lorem ipsum dolor sit amet, consectetur adipiscing elit, sed do eiusmod tempor incidi-dunt ut labore et dolore magna aliqua.</p><div class="mark"><i></i>Redmast</div></article>
    <article class="work-card lift"><div class="photo" role="img" aria-label="Photo of a person writing on a clipboard"></div><h4>Lorem ipsum dolor sit amet con sectetur adipiscing elit.</h4><p>Lorem ipsum dolor sit amet, consectetur adipiscing elit, sed do eiusmod tempor incidi-dunt ut labore et dolore magna aliqua.</p><div class="mark"><i></i>Redmast</div></article>
    <article class="work-card"><div class="photo" role="img" aria-label="Photo of a hand writing on printed pages"></div><h4>Lorem ipsum dolor sit amet con sectetur adipiscing elit.</h4><p>Lorem ipsum dolor sit amet, consectetur adipiscing elit, sed do eiusmod tempor incidi-dunt ut labore et dolore magna aliqua.</p><div class="mark"><i></i>Redmast</div></article>
  </div>
  <span class="btn work-btn">View our work</span>
</section>

<section class="cta">
  <div class="cta-col cta-left" role="img" aria-label="Blue-tinted photo of hands at a desk">
    <h2>Feel free to contact us<br>with any questions.we're<br>happy to help.</h2>
    <p>Lorem ipsum dolor sit amet, consectetur adipiscing elit, sed do eiusmod tempor incididunt ut labore et dolore magna aliqua. Quis ipsum suspendisse ultrices gravida Risus commodo viverra.</p>
    <span class="btn">Get in touch</span>
  </div>
  <div class="cta-col cta-right" role="img" aria-label="Blue-tinted photo of a person at a laptop">
    <h2>Editorial inspiration<br>delivered straight<br>to your inbox.</h2>
    <p>Lorem ipsum dolor sit amet, consectetur adipiscing elit, sed do eiusmod tempor incididunt ut labore et dolore magna aliqua.</p>
    <div class="email">Enter The Email</div>
    <span class="btn">Subscribe</span>
  </div>
</section>

<footer class="site-footer">
  <div class="foot-brand">Penfield Draft<br>Works</div>
  <div class="social" aria-label="Social links"><span></span><span></span><span></span><span></span></div>
  <div class="foot-col" style="left:439px"><h5>Quick links</h5><ul>
    <li><span class="chev">»</span>Home</li><li><span class="chev">»</span>Our Work</li><li><span class="chev">»</span>Capabilities</li><li><span class="chev">»</span>About Us</li><li><span class="chev">»</span>Blog</li></ul></div>
  <div class="foot-col" style="left:603px"><h5>Legal</h5><ul>
    <li><span class="chev">»</span>Privacy Policy</li><li><span class="chev">»</span>Terms &amp; Conditions</li><li><span class="chev">»</span>Contact Us</li><li><span class="chev">»</span>Cookie Policy</li></ul></div>
  <div class="foot-col contact" style="left:808px"><h5>Contact us</h5><ul>
    <li><svg width="12" height="16" viewBox="0 0 12 16"><path d="M6 0a6 6 0 0 0-6 6c0 4.5 6 10 6 10s6-5.5 6-10a6 6 0 0 0-6-6zm0 8.5A2.5 2.5 0 1 1 6 3.5a2.5 2.5 0 0 1 0 5z" fill="#f47b20"/></svg><span>123 Lorem ipsum dolor sit amet<br>consectetur adipiscing elit</span></li>
    <li><svg width="14" height="14" viewBox="0 0 14 14"><path d="M3 0l2.5 3.5-1.5 2a8 8 0 0 0 4.5 4.5l2-1.5L14 11l-2 3C6 14 0 8 0 2z" fill="#f47b20"/></svg><span>123 456 7890</span></li>
    <li><svg width="14" height="11" viewBox="0 0 14 11"><rect width="14" height="11" rx="1" fill="#f47b20"/><path d="M1 1.5l6 4.5 6-4.5" stroke="#fff" stroke-width="1.3" fill="none"/></svg><span>hello@pdworks.net</span></li></ul></div>
</footer>

<div class="copyright">© copyrights 2021 <b>Penfield Draft Works</b> &nbsp;|&nbsp; All Rights Reserved</div>

</body>
</html>
```